Harborview Estates Business Card for Apartment Buildings

Create business cards for resident managers who run apartment buildings. The audience is the public who are searching for apartment rentals, and current residents who live at the apartment building. Key design element will be incorporating the company logo, however, the logo cannot dominate. The building name and manager name are more important than the logo. Current business card design leaves little room for copy, so we may need to reduce the size on the current card to allow for more space for copy.

Target Market(s)

Adults 18-65 years of age, who are looking for an apartment rental, plus current residents who live at our apartment buildings.

Industry/Entity Type

Property Management

Contact Information for Business Card

A major design element will be use of the company logo. Important property and manager contact information must be part of the design. The size of the logo will need to be reduced to make room for building and manager contact copy.

Font styles to use
Sans Serif

Colors
3176b5
000000
959595
ffffff

Requirements
Must have
• 1) Incorporate the company logo.
• 2) Use the company colors (dark blue, black/grey, over white).
• 3) FEATURE THE BUILDING NAME
• 4) FEATURE THE MANAGER NAME
• 5) The company name is less important than BUILDING and MANAGER
• 6) Manager contact information
• **SEE ATTACHED CREATIVE BRIEF**
Nice to have
• 1) Back of card logo watermark
• 2) Ability to write notes on back of carfd
Should not have
• Avoid letting the company logo dominate the card, the building name and manager are more important than the company logo.

```html
<!DOCTYPE html>
<html lang="en">
<head>
<meta charset="utf-8">
<title>Harborview Estates – Resident Manager Business Card</title>
<link href="https://fonts.googleapis.com/css2?family=Roboto:wght@400;500;700&display=swap" rel="stylesheet">
<style>
  :root {
    --brand-blue: #3176b5;
    --band-blue: #1f6fb2;
    --card-grey: #48494d;
    --card-grey-dark: #3f4044;
    --text-light: #e9e9ea;
    --muted: #959595;
    --white: #ffffff;
    --stage: #d9d9d9;
  }
  * { box-sizing: border-box; margin: 0; padding: 0; }
  html, body { width: 1200px; height: 930px; overflow: hidden; }
  body {
    background: var(--stage);
    font-family: "Roboto", Arial, sans-serif;
    position: relative;
  }
  .card {
    position: absolute;
    width: 580px;
    height: 330px;
    border-radius: 20px;
    overflow: hidden;
    background: var(--card-grey);
    box-shadow: 0 6px 18px rgba(0,0,0,.25);
  }
  /* Back of card */
  .card-back { left: 70px; top: 80px; background: linear-gradient(135deg, var(--card-grey) 0%, var(--card-grey-dark) 100%); }
  .card-back .wordmark {
    position: absolute; left: 0; right: 0; top: 118px;
    text-align: center; color: var(--white);
  }
  .wordmark-name {
    font-weight: 700; font-size: 40px; letter-spacing: 1px; line-height: 1;
  }
  .wordmark-sub {
    font-weight: 700; font-size: 16px; letter-spacing: 5px; margin-top: 6px;
  }
  .card-back .website {
    position: absolute; left: 0; right: 0; bottom: 58px;
    text-align: center; color: var(--text-light); font-size: 15px; letter-spacing: .5px;
  }

  /* Front of card */
  .card-front { left: 550px; top: 520px; }
  .name-band {
    position: absolute; left: 0; top: 150px; width: 420px; height: 62px;
    background: var(--band-blue);
  }
  .logo-circle {
    position: absolute; left: 268px; top: -130px; width: 400px; height: 400px;
    border-radius: 50%; background: var(--white);
    border: 9px solid var(--brand-blue);
  }
  .card-front .wordmark {
    position: absolute; left: 322px; top: 100px; width: 250px;
    color: var(--brand-blue); text-align: center;
  }
  .card-front .wordmark-name { font-size: 28px; }
  .card-front .wordmark-sub { font-size: 12px; letter-spacing: 3.5px; margin-top: 5px; }
  .building {
    position: absolute; left: 36px; top: 64px;
    color: var(--text-light); font-size: 15px; line-height: 1.35;
  }
  .manager {
    position: absolute; left: 36px; top: 158px; color: var(--white);
  }
  .manager-name { font-size: 25px; font-weight: 500; line-height: 1.1; }
  .manager-title { font-size: 14px; margin-top: 2px; }
  .contact-list {
    position: absolute; left: 36px; top: 226px; list-style: none;
    color: var(--text-light); font-size: 14px; line-height: 1.25;
  }
  .contact-list li { display: flex; align-items: center; gap: 10px; }
  .contact-list svg { width: 10px; height: 10px; fill: var(--text-light); flex: none; }
</style>
</head>
<body>

  <section class="card card-back" aria-label="Business card back">
    <div class="wordmark">
      <div class="wordmark-name">HARBORVIEW</div>
      <div class="wordmark-sub">ESTATES LLC</div>
    </div>
    <p class="website">www.harborviewest.com</p>
  </section>

  <section class="card card-front" aria-label="Business card front">
    <div class="name-band"></div>
    <div class="logo-circle"></div>
    <div class="wordmark">
      <div class="wordmark-name">HARBORVIEW</div>
      <div class="wordmark-sub">ESTATES LLC</div>
    </div>

    <p class="building">Seabreeze Court Apartments<br>1482 Lindell Avenue<br>Bayside, CA 92190</p>

    <div class="manager">
      <p class="manager-name">Marisol Delgado</p>
      <p class="manager-title">Resident Manager</p>
    </div>

    <ul class="contact-list">
      <li><svg viewBox="0 0 10 10"><path d="M2 0.5 L3.6 2.6 L2.7 3.6 Q4 6.2 6.4 7.3 L7.4 6.4 L9.5 8 L8.4 9.5 Q2.5 8.5 0.5 1.6 Z"/></svg>619-555-0142</li>
      <li><svg viewBox="0 0 10 10"><path d="M2.5 0 H7.5 V10 H2.5 Z M3.4 1 V8 H6.6 V1 Z"/></svg>619-555-0187</li>
      <li><svg viewBox="0 0 10 10"><path d="M2 3 H8 V1 H2 Z M0.5 4 H9.5 V8 H8 V6 H2 V8 H0.5 Z M2.5 7 H7.5 V10 H2.5 Z"/></svg>619-555-0163</li>
      <li><svg viewBox="0 0 10 10"><path d="M0.5 2 H9.5 V8.5 H0.5 Z M1.5 3 L5 5.6 L8.5 3 V7.5 H1.5 Z" fill-rule="evenodd"/></svg>marisol@harborviewest.com</li>
      <li><svg viewBox="0 0 10 10"><circle cx="5" cy="5" r="4.5"/></svg>www.harborviewest.com</li>
    </ul>
  </section>

</body>
</html>
```